Kovát Lillas Physiotherapy Business Card Vienna

We need a business card design for a newly created Physiotherapy company based in Vienna Austria.
We seek a simple, modern, minimalist design without too much color variation. The font should look young/fresh, but definitely not childish or so. Since we are a starting Business, we currently haven't got a logo, if you feel like a logo would fit your design, feel free to use one, but it's not necessary.
Target Market(s)
Healthcare, young and elderly people with mobility issues
Industry/Entity Type
Health And Wellness
Contact Information for Business Card
Name: Lilla Kovát
Title description: Physiotherapist
Phone num: +43 664 2951 4086
e-mail: lilla.praxis@bluemail.example
Colors
Designer to choose colors to be used in the design.
Requirements
Must have
- Final design language must be in German, basically, the Title Description needs to be "Physiotherapeutin" the other details remain as in the English Language.
Nice to have
- Simple, modern, minimalist design
Should not have
- too many colors, Obvious use of a skeleton, skull, spline

```html
<!DOCTYPE html>
<html lang="de">
<head>
<meta charset="utf-8">
<title>Kovát Lillas Physiotherapy – Visitenkarte</title>
<link href="https://fonts.googleapis.com/css2?family=Montserrat:wght@300;400&display=swap" rel="stylesheet">
<style>
  :root {
    --backdrop: #1d1d1d;
    --card: #121212;
    --ink: #f4f4f4;
    --ink-soft: #d9d9d9;
  }
  * { margin: 0; padding: 0; box-sizing: border-box; }
  html, body {
    width: 1200px;
    height: 1200px;
    overflow: hidden;
    background: var(--backdrop);
    font-family: "Montserrat", sans-serif;
    color: var(--ink);
  }
  .sheet {
    width: 1200px;
    height: 1200px;
    display: flex;
    flex-direction: column;
    align-items: center;
    justify-content: center;
    gap: 64px;
  }
  .card {
    width: 740px;
    height: 478px;
    background: var(--card);
    border-radius: 30px;
    box-shadow: 0 18px 40px rgba(0, 0, 0, 0.55);
    display: flex;
    flex-direction: column;
    align-items: center;
    justify-content: center;
    text-align: center;
  }
  .brand-mark {
    width: 112px;
    height: 112px;
    margin-bottom: 22px;
  }
  .brand-name {
    font-size: 32px;
    font-weight: 400;
    letter-spacing: 0.2em;
    text-transform: uppercase;
    padding-left: 0.2em;
  }
  .brand-field {
    font-size: 15px;
    font-weight: 300;
    letter-spacing: 0.55em;
    text-transform: uppercase;
    margin-top: 6px;
    padding-left: 0.55em;
    color: var(--ink-soft);
  }
  .person-name {
    font-size: 44px;
    font-weight: 400;
    letter-spacing: 0.26em;
    text-transform: uppercase;
    padding-left: 0.26em;
  }
  .person-title {
    font-size: 18px;
    font-weight: 300;
    letter-spacing: 0.2em;
    text-transform: uppercase;
    margin-top: 4px;
    padding-left: 0.2em;
    color: var(--ink-soft);
  }
  .divider {
    width: 22px;
    height: 2px;
    background: var(--ink);
    margin: 18px 0 16px;
  }
  .contact-line {
    font-size: 20px;
    font-weight: 300;
    letter-spacing: 0.2em;
    line-height: 1.6;
    padding-left: 0.2em;
  }
  .contact-line.email { letter-spacing: 0.13em; padding-left: 0.13em; }
</style>
</head>
<body>
<main class="sheet">
  <section class="card card-front">
    <svg class="brand-mark" viewBox="0 0 112 112" aria-hidden="true">
      <circle cx="56" cy="56" r="53" fill="none" stroke="#f4f4f4" stroke-width="3"/>
    </svg>
    <h1 class="brand-name">Kovát Lillas</h1>
    <p class="brand-field">Physiotherapy</p>
  </section>

  <section class="card card-back">
    <h2 class="person-name">Lilla Kovát</h2>
    <p class="person-title">Physiotherapeutin</p>
    <span class="divider"></span>
    <p class="contact-line phone">+43 664 2951 4086</p>
    <p class="contact-line email">lilla.praxis@bluemail.example</p>
  </section>
</main>
</body>
</html>
```